Stonebrace Business Card Design

The Stonebrace Co is an aggregate (crushing) equipment dealer serving Western Canadian provinces. Stonebrace is a distributor of aggregate equipment for different manufacturers.

We are looking to change and update the existing business card which has been used since the existence of the company. A copy of existing card has been attached for reference. The Stonebrace Co logo we want to remain the same and we want the green color to remain the same.

We are wanting something new with a different look. A refreshing card to show a new modern and updated look. No longer wanting to have the manufacturers on the back of the card but something more like our logo on the back of the card with a statement like "Rock Ready Supply"

ideas could be:
- card can be different colors on front and back
- front or reverse of the card could possibly be the green color with the logo in black

Target Market(s)

Owners of Aggregate/Crushing companies

Contact Information for Business Card

see above

Requirements
Must have
• - logo to remain same along with same font within logo
• - green color to remain same
Nice to have
• as noted above under project description
Should not have

```html
<!DOCTYPE html>
<html lang="en">
<head>
<meta charset="utf-8">
<title>Stonebrace Co Business Card</title>
<link href="https://fonts.googleapis.com/css2?family=Roboto:wght@400;700&family=Roboto+Condensed:wght@400;700&display=swap" rel="stylesheet">
<style>
  :root{
    --brand-green:#8a8c06;
    --card-white:#f3f3f2;
    --ink:#231f20;
    --text-grey:#4a4a4a;
    --backdrop:#5a4a3b;
  }
  html,body{margin:0;padding:0;overflow:hidden;}
  body{width:1200px;height:960px;background:var(--backdrop);position:relative;font-family:"Roboto",Arial,sans-serif;}
  .card{position:absolute;width:600px;height:343px;border-radius:18px;overflow:hidden;}
  .card-front{left:314px;top:113px;background:var(--card-white);}
  .card-back{left:311px;top:472px;background:var(--brand-green);}
  .band{position:absolute;background:var(--brand-green);}
  .band-top{left:234px;top:0;width:366px;height:38px;border-bottom-left-radius:38px;}
  .band-bottom{left:0;top:292px;width:406px;height:51px;border-top-right-radius:51px;}
  .wordmark{position:absolute;left:36px;top:88px;display:flex;align-items:center;gap:12px;}
  .wordmark-dot{width:22px;height:22px;border-radius:50%;background:var(--brand-green);}
  .wordmark-name{font-weight:700;font-size:16px;color:var(--ink);letter-spacing:0.2px;}
  .contact-block{position:absolute;left:396px;top:77px;}
  .person-name{font-family:"Roboto Condensed",Arial,sans-serif;font-weight:700;font-size:22px;color:var(--brand-green);margin:0;line-height:1;}
  .person-title{font-weight:700;font-size:14px;color:var(--ink);margin:5px 0 0;}
  .contact-list{list-style:none;margin:26px 0 0;padding:0;}
  .contact-list li{display:flex;align-items:center;gap:8px;font-size:14px;color:var(--text-grey);height:19px;}
  .contact-list svg{width:14px;height:14px;fill:var(--brand-green);flex:none;}
  .address{font-size:14px;color:var(--text-grey);margin:10px 0 0;line-height:19px;}
  .website{position:absolute;left:43px;top:310px;font-size:15px;color:#fff;letter-spacing:5.2px;}
  .back-mark{position:absolute;left:0;right:0;top:142px;display:flex;justify-content:center;align-items:center;gap:16px;}
  .back-dot{width:40px;height:40px;border-radius:50%;background:var(--ink);}
  .back-name{font-weight:700;font-size:40px;color:var(--ink);}
  .tagline{position:absolute;left:0;right:0;top:290px;text-align:center;font-family:"Roboto Condensed",Arial,sans-serif;font-weight:700;font-size:16px;color:var(--ink);letter-spacing:0.6px;}
</style>
</head>
<body>
  <section class="card card-front">
    <div class="band band-top" role="img" aria-label="Green decorative band"></div>
    <div class="band band-bottom" role="img" aria-label="Green decorative band"></div>
    <div class="wordmark">
      <span class="wordmark-dot"></span>
      <span class="wordmark-name">THE STONEBRACE CO.</span>
    </div>
    <div class="contact-block">
      <p class="person-name">DALE MORROW</p>
      <p class="person-title">CEO/FOUNDER</p>
      <ul class="contact-list">
        <li><svg viewBox="0 0 24 24"><path d="M6.6 10.8a15.2 15.2 0 0 0 6.6 6.6l2.2-2.2c.3-.3.7-.4 1-.2 1.1.4 2.3.6 3.6.6.6 0 1 .4 1 1V20c0 .6-.4 1-1 1A17 17 0 0 1 3 4c0-.6.4-1 1-1h3.5c.6 0 1 .4 1 1 0 1.3.2 2.5.6 3.6.1.3 0 .7-.2 1z"/></svg>780.555.0142</li>
        <li><svg viewBox="0 0 24 24"><path d="M7 1h10a2 2 0 0 1 2 2v18a2 2 0 0 1-2 2H7a2 2 0 0 1-2-2V3a2 2 0 0 1 2-2zm0 3v14h10V4z"/></svg>780.555.0187</li>
        <li><svg viewBox="0 0 24 24"><path d="M6 2h12v6H6zM3 9h18a1 1 0 0 1 1 1v8h-4v4H6v-4H2v-8a1 1 0 0 1 1-1zm5 7v4h8v-4z"/></svg>780.555.0163</li>
        <li><svg viewBox="0 0 24 24"><path d="M2 5h20v14H2zm2 2v.5l8 5 8-5V7z"/></svg>dale@stonebr.com</li>
      </ul>
      <p class="address">2290- 48B Avenue<br>Nisku, Alberta T9E 5K2</p>
    </div>
    <div class="website">www.stonebrace.ca</div>
  </section>

  <section class="card card-back">
    <div class="back-mark">
      <span class="back-dot"></span>
      <span class="back-name">STONEBRACE CO.</span>
    </div>
    <div class="tagline">ROCK READY SUPPLY</div>
  </section>
</body>
</html>
```